Local Motorsports Photography Business Card Design

Looking for a Logo and Business Card design for my father who is a local photographer based in Perth operating under the business name "Kelmor Photography". Specializing in Motorsports (Turbo Racers/Rapidcycles/Corvan Rally) and events photography.
Would like it to look professional, while still maintaining a local/personal feel. Color\Design of the Logo and Card are open to your own interpretation, but should limit the color scheme to around 2-3 colors.
Design should be a logo one side and contact details on the rear. The website currently is very simple and a generic template and should not be used as a basis for design.
Industry/Entity Type
Business
Contact Information for Business Card
Name: Marcus Pellman
Website: www.klmphotography-example.com.au
Email: marcus@klmphotography-example.com.au
Phone: 0400 555 917

```html
<!DOCTYPE html>
<html lang="en">
<head>
<meta charset="utf-8">
<title>Kelmor Photography – Business Card</title>
<link rel="stylesheet" href="https://fonts.googleapis.com/css2?family=Exo+2:wght@400;500;600&display=swap">
<style>
  :root {
    --page-bg: #e4e6e8;
    --card-white: #f8f8f8;
    --card-grey: #e3e4e5;
    --brand-green: #1ea24e;
    --accent-lime: #9ccf3c;
    --ink: #2b2b2b;
  }
  * { box-sizing: border-box; margin: 0; padding: 0; }
  html, body {
    width: 1200px; height: 864px; overflow: hidden;
    background: var(--page-bg);
    font-family: "Exo 2", sans-serif;
  }
  .card {
    position: absolute; left: 75px; top: 132px;
    width: 1050px; height: 600px;
    background: radial-gradient(ellipse at 60% 35%, var(--card-white) 0%, var(--card-grey) 100%);
    overflow: hidden;
    box-shadow: 0 10px 30px rgba(0,0,0,0.18);
  }
  .card-shapes { position: absolute; inset: 0; }
  .brand {
    position: absolute; right: 60px; top: 70px;
    display: flex; align-items: center; gap: 12px;
  }
  .brand-mark {
    width: 22px; height: 22px; border-radius: 50%;
    background: var(--brand-green);
  }
  .brand-name {
    font-size: 30px; font-weight: 500; color: var(--brand-green);
    letter-spacing: 1px; white-space: nowrap; text-transform: uppercase;
  }
  .address {
    position: absolute; right: 60px; top: 128px;
    font-size: 21px; line-height: 28px; color: var(--ink); text-align: right;
  }
  .contact-list {
    position: absolute; right: 50px; top: 210px;
    list-style: none;
    font-size: 16px; line-height: 30px; color: var(--ink);
  }
  .contact-list li { display: flex; justify-content: flex-end; align-items: center; gap: 10px; }
  .contact-list svg { width: 17px; height: 17px; flex: none; }
  .person {
    position: absolute; left: 110px; top: 445px; color: #fff;
  }
  .person-name { font-size: 29px; font-weight: 500; letter-spacing: 1px; text-transform: uppercase; }
  .person-title { font-size: 20px; margin-top: 2px; padding-left: 40px; }
</style>
</head>
<body>
<div class="card">
  <svg class="card-shapes" viewBox="0 0 1050 600" width="1050" height="600" aria-hidden="true">
    <path d="M0,0 H380 L720,420 Q620,500 580,600 H0 Z" fill="var(--brand-green)"/>
    <ellipse cx="700" cy="205" rx="505" ry="235" fill="var(--accent-lime)"/>
    <ellipse cx="722" cy="196" rx="495" ry="228" fill="#ffffff"/>
    <ellipse cx="730" cy="190" rx="490" ry="224" fill="var(--card-white)"/>
  </svg>

  <div class="brand">
    <span class="brand-mark"></span>
    <span class="brand-name">Kelmor Photography</span>
  </div>

  <p class="address">061.12th floor Plaza<br>Harbour Road PTH</p>

  <ul class="contact-list">
    <li>0400 555 917
      <svg viewBox="0 0 24 24"><path d="M6.6 10.8a15 15 0 0 0 6.6 6.6l2.2-2.2a1 1 0 0 1 1-.25 11.4 11.4 0 0 0 3.6.57 1 1 0 0 1 1 1V20a1 1 0 0 1-1 1A17 17 0 0 1 3 4a1 1 0 0 1 1-1h3.5a1 1 0 0 1 1 1c0 1.25.2 2.45.57 3.6a1 1 0 0 1-.25 1z" fill="var(--brand-green)"/></svg>
    </li>
    <li>0400 555 917
      <svg viewBox="0 0 24 24"><rect x="7" y="2" width="10" height="20" rx="2" fill="none" stroke="var(--brand-green)" stroke-width="2"/><circle cx="12" cy="18" r="1.2" fill="var(--brand-green)"/></svg>
    </li>
    <li>0400 555 917
      <svg viewBox="0 0 24 24"><rect x="3" y="9" width="18" height="12" rx="1" fill="var(--brand-green)"/><rect x="7" y="3" width="10" height="7" fill="none" stroke="var(--brand-green)" stroke-width="2"/></svg>
    </li>
    <li>marcus@kelmorphotography-example.com.au
      <svg viewBox="0 0 24 24"><rect x="2" y="5" width="20" height="14" rx="1" fill="var(--brand-green)"/><path d="M3 6l9 7 9-7" fill="none" stroke="#fff" stroke-width="1.6"/></svg>
    </li>
    <li>www.kelmorphotography-example.com.au
      <svg viewBox="0 0 24 24"><circle cx="12" cy="12" r="10" fill="var(--brand-green)"/><path d="M2 12h20M12 2c3 3 3 17 0 20M12 2c-3 3-3 17 0 20" fill="none" stroke="#fff" stroke-width="1.3"/></svg>
    </li>
  </ul>

  <div class="person">
    <div class="person-name">Marcus Pellman</div>
    <div class="person-title">Managing Director</div>
  </div>
</div>
</body>
</html>
```